Salon and Spa Distributor Business Card

Need a business card. We are are distributor in the salon and spa industry. We identify with natural beauty. Need a card with:
Company Name: Petal Quarry"
Title: "President & CEO"
Address
Company Phone number
email
website
Tag Line:" The Professional Salon Source"

Industry/Entity Type

Business

Contact Information for Business Card

Name: Dov Strommen
Title: "President & CEO"
Address: 31 Harlow Ln, Bexmoor, NJ 07813
Company Phone number: 800-463-5918
email: dovstrommen@petalquarry.example
website: www.petalquarry.example

Requirements
Should not have
• No black backgrounds

```html
<!DOCTYPE html>
<html lang="en">
<head>
<meta charset="utf-8">
<title>Petal Quarry — Business Card</title>
<link rel="stylesheet" href="https://fonts.googleapis.com/css2?family=Open+Sans:wght@300;400;700&display=swap">
<style>
  :root {
    --backdrop: #3b3531;
    --card: #f5f7ef;
    --card-edge: #e3e8d8;
    --green: #3f9a2c;
    --green-bright: #46a832;
    --ink: #2a2d28;
  }
  * { box-sizing: border-box; margin: 0; padding: 0; }
  html, body { width: 1200px; height: 844px; overflow: hidden; }
  body {
    background: var(--backdrop);
    font-family: "Open Sans", Arial, sans-serif;
    position: relative;
  }
  .card {
    position: absolute;
    top: 268px;
    width: 540px;
    height: 309px;
    background: var(--card);
    border: 1px solid var(--card-edge);
    border-radius: 3px;
    box-shadow: 0 10px 28px rgba(0,0,0,0.45);
    overflow: hidden;
  }
  .card--front { left: 40px; }
  .card--back { left: 620px; }

  .brand {
    position: absolute;
    display: flex;
    align-items: center;
    gap: 12px;
  }
  .brand__dot {
    width: 34px; height: 34px;
    border-radius: 50%;
    background: var(--green);
    flex: none;
  }
  .brand__name {
    font-weight: 300;
    font-size: 30px;
    color: var(--green);
    letter-spacing: 0.2px;
    white-space: nowrap;
  }
  .card--front .brand { left: 112px; top: 70px; }

  .contact {
    position: absolute;
    right: 24px;
    top: 178px;
    list-style: none;
    text-align: right;
    color: var(--ink);
    font-size: 14.5px;
    line-height: 22px;
  }
  .contact li { display: flex; align-items: center; justify-content: flex-end; gap: 6px; }
  .contact svg { width: 11px; height: 11px; fill: var(--green); flex: none; }

  .person {
    position: absolute;
    left: 30px;
    top: 200px;
    color: var(--ink);
  }
  .person__name {
    font-weight: 700;
    font-size: 18px;
    color: var(--green-bright);
    line-height: 22px;
  }
  .person__title { font-size: 14.5px; line-height: 20px; }
  .person__address { font-size: 14.5px; line-height: 22px; margin-top: 10px; }

  .card--back .brand { left: 50%; top: 96px; transform: translateX(-50%); }
  .tagline {
    position: absolute;
    left: 0; right: 0;
    top: 186px;
    text-align: center;
    font-weight: 700;
    font-size: 16px;
    color: var(--green);
  }
</style>
</head>
<body>
  <section class="card card--front" aria-label="Business card front">
    <div class="brand">
      <span class="brand__dot"></span>
      <span class="brand__name">Petal Quarry</span>
    </div>
    <ul class="contact">
      <li>800-463-5918
        <svg viewBox="0 0 24 24" aria-hidden="true"><path d="M6.6 10.8a15 15 0 0 0 6.6 6.6l2.2-2.2a1 1 0 0 1 1-.25 11.4 11.4 0 0 0 3.6.57 1 1 0 0 1 1 1V20a1 1 0 0 1-1 1A17 17 0 0 1 3 4a1 1 0 0 1 1-1h3.5a1 1 0 0 1 1 1c0 1.25.2 2.45.57 3.57a1 1 0 0 1-.25 1z"/></svg>
      </li>
      <li>dovstrommen@petalquarry.example
        <svg viewBox="0 0 24 24" aria-hidden="true"><path d="M2 5h20v14H2zm2 2v.5l8 5 8-5V7l-8 5z"/></svg>
      </li>
      <li>www.petalquarry.example
        <svg viewBox="0 0 24 24" aria-hidden="true"><circle cx="12" cy="12" r="10"/></svg>
      </li>
    </ul>
    <div class="person">
      <p class="person__name">Dov Strommen</p>
      <p class="person__title">President &amp; CEO</p>
      <p class="person__address">31 Harlow Ln,<br>Bexmoor, NJ 07813</p>
    </div>
  </section>

  <section class="card card--back" aria-label="Business card back">
    <div class="brand">
      <span class="brand__dot"></span>
      <span class="brand__name">Petal Quarry</span>
    </div>
    <p class="tagline">The Professional Salon Source</p>
  </section>
</body>
</html>
```